BOLD & MINIMALIST DESIGN NEEDED

We want a very bold but minimalistic business card design that is impactful and utilizes both sides of the business card. Our current logo is included for your use.

We want bold fonts and good use of negative space. We don't want the logo to overpower the design.

Target Market(s)

Professionals who are building new commercial buildings.

Industry/Entity Type

Construction

Contact Information for Business Card

Name, Title, email, office phone, cell phone, website

Font styles to use
Serif
Sans Serif

Requirements
Must have
• Bold design!

```html
<!DOCTYPE html>
<html lang="en">
<head>
<meta charset="utf-8">
<title>Ridgecrest Business Card</title>
<link rel="stylesheet" href="https://fonts.googleapis.com/css2?family=Poppins:wght@400;500;700&display=swap">
<style>
  :root {
    --backdrop: #262626;
    --card-dark: #1f1f1f;
    --card-light: #ededed;
    --ink: #1c1c1c;
    --ink-soft: #2a2a2a;
    --accent: #7cb82f;
    --mute: #cfcfcf;
    --wordmark-dark: #6a6a6a;
  }
  * { margin: 0; padding: 0; box-sizing: border-box; }
  html, body { width: 1200px; height: 576px; overflow: hidden; }
  body {
    background: var(--backdrop);
    font-family: "Poppins", sans-serif;
    position: relative;
  }
  .card {
    position: absolute;
    top: 138px;
    border-radius: 10px;
  }
  .card-back {
    left: 102px;
    width: 484px;
    height: 294px;
    background: var(--card-dark);
  }
  .card-front {
    left: 596px;
    width: 480px;
    height: 291px;
    background: var(--card-light);
  }
  .back-wordmark {
    position: absolute;
    left: 0; right: 0;
    top: 108px;
    text-align: center;
    font-weight: 700;
    font-size: 48px;
    letter-spacing: 2px;
    color: var(--wordmark-dark);
    text-transform: uppercase;
  }
  .back-url {
    position: absolute;
    left: 0; right: 0;
    top: 252px;
    text-align: center;
    font-size: 13px;
    letter-spacing: 7px;
    color: var(--mute);
  }
  .brand {
    position: absolute;
    left: 52px;
    top: 126px;
    display: flex;
    align-items: center;
    gap: 8px;
  }
  .brand-mark {
    width: 18px; height: 18px;
    background: var(--accent);
  }
  .brand-name {
    font-weight: 700;
    font-size: 26px;
    color: var(--ink);
    text-transform: uppercase;
    letter-spacing: 0.5px;
  }
  .person {
    position: absolute;
    left: 266px;
    top: 90px;
  }
  .person-name {
    font-weight: 500;
    font-size: 20px;
    color: var(--accent);
    line-height: 1.2;
  }
  .person-title {
    font-size: 11.5px;
    color: var(--ink-soft);
    margin-top: 2px;
  }
  .contacts {
    position: absolute;
    left: 268px;
    top: 150px;
    list-style: none;
  }
  .contacts li {
    display: flex;
    align-items: center;
    gap: 8px;
    font-size: 12px;
    color: var(--ink-soft);
    height: 17px;
  }
  .contacts svg { width: 10px; height: 10px; fill: var(--accent); flex: none; }
</style>
</head>
<body>
  <section class="card card-back">
    <div class="back-wordmark">Ridgecrest</div>
    <div class="back-url">www.ridgecrest.com</div>
  </section>

  <section class="card card-front">
    <div class="brand">
      <span class="brand-mark"></span>
      <span class="brand-name">Ridgecrest</span>
    </div>
    <div class="person">
      <div class="person-name">Daniel Reyes</div>
      <div class="person-title">Director</div>
    </div>
    <ul class="contacts">
      <li>
        <svg viewBox="0 0 10 10" aria-hidden="true"><path d="M1 3c0-1 1-2 4-2s4 1 4 2v1H7V3H3v1H1z M2 5h6l1 4H1z"/></svg>
        004-004-0004
      </li>
      <li>
        <svg viewBox="0 0 10 10" aria-hidden="true"><path d="M0 2h10v6H0z" /><path d="M0 2l5 3.5L10 2" stroke="#ededed" stroke-width="1" fill="none"/></svg>
        dan@ridgecrest.com
      </li>
      <li>
        <svg viewBox="0 0 10 10" aria-hidden="true"><circle cx="5" cy="5" r="4.5"/><path d="M0.5 5h9M5 0.5v9" stroke="#ededed" stroke-width="0.8"/></svg>
        www.ridgecrest.com
      </li>
    </ul>
  </section>
</body>
</html>
```